Existing Website Requiring new Pages

I have an existing word press website that was built using elementor.
Website: www.tallowcrestcare.com.au
I require the Vacancies page (https://www.tallowcrestcare.com.au/vacancies/) to be modified to display our new properties along with minor tweaks to how the information is presented.
The vacancies to be displayed are the exactly the same as those that are located on the homepage of QMR website (https://qmr.org.au/)
The new pages that link off the Vacancies tab will require custom design.
There are roughly 8 pages/properties to be incorporated. i wish for the design to be very similar to that displayed in the following link; https://www.polunda.com.au/vacancies/merrylands
Along with this the back end has not been updated for the last 3 years so it also requires some maintenance.
Website is in the disability industry and the custom pages will display information relative to Property Vacancies.
I have attached a ZIP file with some design guides, the information for each of the properties (which will need to be modified to show our business name Tallowcrest Care) and the example of how it is to look based off the Polunda website.
If you guys have any suggestions or ideas on how to make this more presentable or possible i'm open to your ideas.
Target Market(s)
People looking for SDA properties custom built for people with a disability
Industry/Entity Type
Disability
Coding
Coded - Design and coding required
Number of Pages Required
5+ page

```html
<!DOCTYPE html>
<html lang="en">
<head>
<meta charset="utf-8">
<title>Vacancies – Tallowcrest Care</title>
<link href="https://fonts.googleapis.com/css2?family=Archivo:wght@700;800;900&family=Montserrat:wght@400;500;600;700&family=Work+Sans:wght@400;500&display=swap" rel="stylesheet">
<style>
:root{
  --teal:#05d5b2;
  --yellow:#fcc24c;
  --orange:#f0843c;
  --ink:#1f2125;
  --nav:#3a3a3a;
  --muted:#8a8a8a;
  --line:#c9c9c9;
  --tag-bg:#fff4e4;
  --pink:#e0468a;
  --blue:#2f7de1;
  --icon-dark:#1b1b1b;
  --bar:#1e1e1e;
}
*{box-sizing:border-box;margin:0;padding:0}
html,body{width:1200px;height:2834px;overflow:hidden;background:#fff}
body{position:relative;font-family:"Montserrat",sans-serif;color:var(--ink)}
a{color:inherit;text-decoration:none}

.site-header{position:absolute;left:0;top:0;width:1200px;height:125px;background:#fff}
.brand{position:absolute;left:141px;top:36px;display:flex;align-items:center;gap:8px;font-family:"Montserrat",sans-serif;font-weight:700;font-size:17px;color:var(--teal)}
.brand-dot{width:30px;height:30px;border-radius:50%;background:var(--teal)}
.main-nav{position:absolute;top:52px;left:565px;display:flex;font-size:10.5px;font-weight:700;letter-spacing:.6px;color:var(--nav)}
.main-nav a{margin-right:22px}
.main-nav .active{color:var(--orange)}

.hero{position:absolute;left:0;top:125px;width:1200px;height:446px;overflow:hidden}
.hero-photo{position:absolute;inset:0;background:linear-gradient(110deg,#d9dde1 0%,#b9c2c9 45%,#8e979f 75%,#5c6166 100%)}
.hero-shape{position:absolute;inset:0}
.hero-title{position:absolute;left:108px;top:188px;font-family:"Archivo",sans-serif;font-weight:900;font-size:62px;color:#fff;letter-spacing:.5px}

.vacancy-grid{position:absolute;left:0;top:0}
.card{position:absolute;width:436px}
.card-photo{height:286px;border-radius:5px 5px 0 0;border:1px solid var(--line)}
.card-info{margin-top:3px;height:114px;border:1px solid var(--line);border-radius:0 0 5px 5px;background:#fff;text-align:center;padding-top:18px}
.card-title{font-family:"Archivo",sans-serif;font-weight:700;font-size:24px;letter-spacing:.3px;color:var(--ink)}
.card-tag{display:inline-flex;align-items:center;gap:10px;margin-top:10px;height:35px;padding:0 24px;background:var(--tag-bg);border-radius:4px;font-family:"Work Sans",sans-serif;font-size:16px;color:var(--ink);letter-spacing:.3px}

.dots{position:absolute}

.site-footer{position:absolute;left:0;top:2486px;width:1200px;height:284px;background:#fff;box-shadow:0 -4px 10px rgba(0,0,0,.04)}
.footer-brand{position:absolute;left:112px;top:80px;display:flex;align-items:center;gap:8px;font-weight:700;font-size:19px;color:var(--teal)}
.contact-list{position:absolute;left:110px;top:196px;list-style:none;font-size:12.5px;color:var(--muted)}
.contact-list li{display:flex;align-items:center;gap:8px;height:22px}
.social{position:absolute;left:515px;top:55px;display:flex;flex-direction:column;gap:10px}
.social span{width:31px;height:31px;border-radius:50%;display:block}
.footer-col{position:absolute;top:50px;width:225px;font-size:12.5px;color:var(--muted)}
.footer-col h3{font-weight:500;font-size:14px;color:var(--ink);border-left:3px solid var(--blue);padding-left:12px;height:16px;line-height:16px;margin-bottom:14px}
.footer-col ul{list-style:none;border-top:1px solid #e6e6e6}
.footer-col li{border-bottom:1px solid #e6e6e6;padding:8px 0;line-height:22px}
.copyright{position:absolute;left:0;top:2770px;width:1200px;height:64px;background:var(--bar);color:#fff;font-size:13.5px;display:flex;align-items:center;justify-content:center}
.copyright b{text-decoration:underline;margin:0 4px}
</style>
</head>
<body>

<header class="site-header">
  <a class="brand" href="#"><span class="brand-dot"></span>Tallowcrest Care</a>
  <nav class="main-nav">
    <a href="#">HOME</a>
    <a href="#">ABOUT US</a>
    <a href="#" class="active">WHAT WE DO ⌄</a>
    <a href="#">REFERRALS</a>
    <a href="#">FEEDBACK</a>
    <a href="#">CONTACT US</a>
  </nav>
</header>

<section class="hero">
  <div class="hero-photo" role="img" aria-label="Smiling man in a wheelchair holding a tablet in a bright office"></div>
  <svg class="hero-shape" width="1200" height="446" viewBox="0 0 1200 446">
    <polygon points="0,0 424,0 574,223 424,446 0,446" fill="var(--teal)"/>
    <polygon points="424,446 574,243 574,272 448,446" fill="var(--yellow)"/>
  </svg>
  <h1 class="hero-title">VACANCIES</h1>
</section>

<svg class="dots" style="left:117px;top:633px" width="168" height="165">
  <defs><pattern id="dotgrid" width="8" height="8" patternUnits="userSpaceOnUse"><circle cx="2" cy="2" r="1.2" fill="#222"/></pattern></defs>
  <rect x="0" y="0" width="166" height="24" fill="url(#dotgrid)"/>
  <rect x="0" y="24" width="24" height="140" fill="url(#dotgrid)"/>
</svg>
<svg class="dots" style="left:918px;top:2234px" width="168" height="165">
  <defs><pattern id="dotgrid2" width="8" height="8" patternUnits="userSpaceOnUse"><circle cx="2" cy="2" r="1.2" fill="#222"/></pattern></defs>
  <rect x="140" y="0" width="24" height="140" fill="url(#dotgrid2)"/>
  <rect x="0" y="140" width="166" height="24" fill="url(#dotgrid2)"/>
</svg>

<main class="vacancy-grid">
  <article class="card" style="left:144px;top:660px">
    <div class="card-photo" role="img" aria-label="Single-storey rendered house with garage" style="background:linear-gradient(180deg,#e4e8ee 0%,#cfd4d8 45%,#7f8a6e 70%,#6d6a66 100%)"></div>
    <div class="card-info"><h2 class="card-title">PENRITH</h2><span class="card-tag"><svg width="18" height="12" viewBox="0 0 18 12"><path d="M1 1v10M1 8h16v3M1 6h16M4 4h4v2H4z" stroke="var(--yellow)" stroke-width="2" fill="none"/></svg>4 Bedroom SIL Home</span></div>
  </article>
  <article class="card" style="left:620px;top:660px">
    <div class="card-photo" role="img" aria-label="Brick house with red roof and paved driveway" style="background:linear-gradient(180deg,#a9c8e6 0%,#b87060 35%,#5c8a3e 60%,#c2826a 100%)"></div>
    <div class="card-info"><h2 class="card-title">MOUNT DRUITT</h2><span class="card-tag"><svg width="18" height="12" viewBox="0 0 18 12"><path d="M1 1v10M1 8h16v3M1 6h16M4 4h4v2H4z" stroke="var(--yellow)" stroke-width="2" fill="none"/></svg>4 Bedroom SIL Home</span></div>
  </article>

  <article class="card" style="left:144px;top:1098px">
    <div class="card-photo" role="img" aria-label="Cream brick house with dark tiled roof" style="background:linear-gradient(180deg,#4a9fe0 0%,#8fc4ef 30%,#d8c9a4 55%,#5f8a3a 75%,#c7b99a 100%)"></div>
    <div class="card-info"><h2 class="card-title">CASULA</h2><span class="card-tag"><svg width="18" height="12" viewBox="0 0 18 12"><path d="M1 1v10M1 8h16v3M1 6h16M4 4h4v2H4z" stroke="var(--yellow)" stroke-width="2" fill="none"/></svg>4 Bedroom SIL Home</span></div>
  </article>
  <article class="card" style="left:620px;top:1098px">
    <div class="card-photo" role="img" aria-label="Federation-style cottage with blue shutters" style="background:linear-gradient(180deg,#e9eef2 0%,#e2d3b8 40%,#d9c6a6 70%,#7f8a5c 100%)"></div>
    <div class="card-info"><h2 class="card-title">EASTWOOD</h2><span class="card-tag"><svg width="18" height="12" viewBox="0 0 18 12"><path d="M1 1v10M1 8h16v3M1 6h16M4 4h4v2H4z" stroke="var(--yellow)" stroke-width="2" fill="none"/></svg>4 Bedroom SIL Home</span></div>
  </article>

  <article class="card" style="left:144px;top:1535px">
    <div class="card-photo" role="img" aria-label="Brick house with double garage and palm tree" style="background:linear-gradient(180deg,#8ab9e4 0%,#c7dbea 30%,#c49a7c 55%,#56a13a 80%,#c9b8a6 100%)"></div>
    <div class="card-info"><h2 class="card-title">BAULKHAM HILLS</h2><span class="card-tag"><svg width="18" height="12" viewBox="0 0 18 12"><path d="M1 1v10M1 8h16v3M1 6h16M4 4h4v2H4z" stroke="var(--yellow)" stroke-width="2" fill="none"/></svg>4 Bedroom SIL Home</span></div>
  </article>
  <article class="card" style="left:620px;top:1535px">
    <div class="card-photo" role="img" aria-label="Orange brick house with wide driveway and lawn" style="background:linear-gradient(180deg,#9cc6ea 0%,#d5e3ee 30%,#cf6a3a 52%,#5fa63c 72%,#bdb8b0 100%)"></div>
    <div class="card-info"><h2 class="card-title">MERRYLANDS</h2><span class="card-tag"><svg width="18" height="12" viewBox="0 0 18 12"><path d="M1 1v10M1 8h16v3M1 6h16M4 4h4v2H4z" stroke="var(--yellow)" stroke-width="2" fill="none"/></svg>4 Bedroom SIL Home</span></div>
  </article>

  <article class="card" style="left:144px;top:1973px">
    <div class="card-photo" role="img" aria-label="Large two-storey rendered house with columns" style="background:linear-gradient(180deg,#2c64b8 0%,#4f86cf 30%,#ddd2c6 55%,#3f7a2c 78%,#5da13a 100%)"></div>
    <div class="card-info"><h2 class="card-title">LOREM IPSUM DOLOR</h2><span class="card-tag"><svg width="18" height="12" viewBox="0 0 18 12"><path d="M1 1v10M1 8h16v3M1 6h16M4 4h4v2H4z" stroke="var(--yellow)" stroke-width="2" fill="none"/></svg>4 Bedroom SIL Home</span></div>
  </article>
  <article class="card" style="left:620px;top:1973px">
    <div class="card-photo" role="img" aria-label="Two-storey stone and brick house among trees" style="background:linear-gradient(180deg,#dfe6e4 0%,#7f9a6a 25%,#6e5446 50%,#514038 75%,#4f8a30 100%)"></div>
    <div class="card-info"><h2 class="card-title">LOREM IPSUM DOLOR</h2><span class="card-tag"><svg width="18" height="12" viewBox="0 0 18 12"><path d="M1 1v10M1 8h16v3M1 6h16M4 4h4v2H4z" stroke="var(--yellow)" stroke-width="2" fill="none"/></svg>4 Bedroom SIL Home</span></div>
  </article>
</main>

<footer class="site-footer">
  <div class="footer-brand"><span class="brand-dot"></span>Tallowcrest Care</div>
  <ul class="contact-list">
    <li><svg width="14" height="11" viewBox="0 0 14 11"><rect x="1" y="1" width="12" height="9" rx="1" fill="none" stroke="var(--pink)" stroke-width="1.3"/><path d="M1 2l6 4 6-4" fill="none" stroke="var(--pink)" stroke-width="1.3"/></svg>Email: info@tallowcrestcare.com.au</li>
    <li><svg width="14" height="14" viewBox="0 0 24 24"><path d="M6.6 10.8a15 15 0 006.6 6.6l2.2-2.2a1 1 0 011-.25 11.4 11.4 0 003.6.57 1 1 0 011 1V20a1 1 0 01-1 1A17 17 0 013 4a1 1 0 011-1h3.5a1 1 0 011 1c0 1.25.2 2.45.57 3.57a1 1 0 01-.25 1z" fill="var(--pink)"/></svg>Phone: +61 0491 570 156</li>
    <li><svg width="14" height="14" viewBox="0 0 14 14"><circle cx="7" cy="7" r="5.8" fill="none" stroke="var(--pink)" stroke-width="1.3"/><path d="M7 3.5V7l2.5 1.5" fill="none" stroke="var(--pink)" stroke-width="1.3"/></svg>Operating Hours: 9AM To 5PM Monday - Friday</li>
  </ul>
  <div class="social">
    <span style="background:#7a3a8f"></span>
    <span style="background:#3b5c9e"></span>
    <span style="background:var(--icon-dark)"></span>
    <span style="background:#1c73b4"></span>
  </div>
  <div class="footer-col" style="left:605px">
    <h3>ACCOMMODATION</h3>
    <ul>
      <li>Supported Independent Living (SIL)</li>
      <li>Specialist Disability<br>Accommodation (SDA)</li>
      <li>Short term Accommodation<br>(Respite)</li>
      <li>Vacancies</li>
    </ul>
  </div>
  <div class="footer-col" style="left:853px">
    <h3>WHAT WE DO</h3>
    <ul>
      <li>In Home Care</li>
      <li>Social &amp; Community Services</li>
      <li>Therapeutic Supports</li>
      <li>Support Coordination</li>
      <li>Home Modifications</li>
    </ul>
  </div>
</footer>

<div class="copyright">© Copyrights 2024 <b>Tallowcrest Care</b> | All Rights Reserved</div>

</body>
</html>
```